Custom T Shirt Site Needs New Graphics for Homepage.

I am looking to have the homepage graphic redone. They need to unique images and give the site a fresh look. www.pennolark.com. I want new banners, New images for T Shirts, Polo Shirts, Sweatshirts, Hats, Jersey. I want the large banner on the homepage changed and the 3 banners to the right and below. I would look at a new layout of the homepage.

```html
<!DOCTYPE html>
<html lang="en">
<head>
<meta charset="utf-8">
<title>Pennolark — Custom T-Shirts Online</title>
<link href="https://fonts.googleapis.com/css2?family=Lato:wght@300;400;700&family=Yanone+Kaffeesatz:wght@400;500&display=swap" rel="stylesheet">
<style>
:root{
  --sky-top:#8fe6fb;
  --sky-bottom:#2db4d9;
  --nav:#1d6e8c;
  --nav-dark:#174f66;
  --teal-text:#1a7fa5;
  --link-light:#d9f5ff;
  --olive:#a9b55b;
  --olive-light:#b6c27a;
  --ink:#222;
  --body:#555;
  --tile-red:#c83c44;
  --tile-gold:#fbab0f;
  --tile-blue:#1d7cb0;
  --grey-band:#f1f0f0;
  --footer:#2e2e2e;
  --white:#fff;
}
*{margin:0;padding:0;box-sizing:border-box}
html,body{width:1016px;height:1200px;overflow:hidden;background:var(--white)}
body{position:relative;font-family:'Lato',sans-serif;color:var(--body)}
a{color:inherit;text-decoration:none}

.masthead{position:absolute;left:0;top:0;width:1016px;height:98px;background:linear-gradient(var(--sky-top),var(--sky-bottom))}
.brand{position:absolute;left:102px;top:26px;display:flex;align-items:center;gap:8px;color:var(--white);font-size:34px;font-weight:400;letter-spacing:-.5px}
.brand-dot{width:12px;height:12px;border-radius:50%;background:var(--white)}
.contact-row{position:absolute;right:112px;top:28px;display:flex;align-items:center;gap:10px}
.phone{font-size:16px;font-weight:700;color:#1b5f7a;margin-right:8px}
.chat{display:flex;align-items:center;gap:7px;font-size:12px;color:#1b5f7a;margin-right:12px}
.social{width:19px;height:19px;border-radius:50%}
.top-links{position:absolute;right:112px;top:68px;display:flex;gap:34px;font-size:12px;color:var(--link-light)}

.mainnav{position:absolute;left:0;top:98px;width:1016px;height:51px;background:linear-gradient(var(--nav),var(--nav-dark));border-bottom:1px solid #0f3647}
.category-links{position:absolute;left:102px;top:18px;display:flex;gap:38px;font-size:12px;color:var(--white)}
.account-links{position:absolute;right:102px;top:17px;display:flex;gap:8px;font-size:10.5px;color:var(--white);align-items:center}
.account-links .sep{opacity:.7}

.hero{position:absolute;left:0;top:149px;width:1016px;height:326px;background:radial-gradient(ellipse at 60% 40%,#fbfbfb,#e8e8e8 70%,#dcdcdc)}
.hero-photo{position:absolute;left:103px;top:70px;width:223px;height:256px;border-radius:90px 90px 0 0;background:linear-gradient(#d9c2aa,#b9a796 45%,#9aa0a6)}
.hero-title{position:absolute;left:362px;top:60px;font-family:'Yanone Kaffeesatz',sans-serif;font-weight:500;font-size:56px;color:var(--olive);letter-spacing:1px;line-height:1}
.hero-sub{position:absolute;left:363px;top:135px;font-size:30px;font-weight:400;color:var(--ink)}
.hero-tag{position:absolute;left:362px;top:193px;font-size:31px;font-weight:300;color:var(--olive-light)}
.trust-badge{position:absolute;left:572px;top:192px;width:70px;height:70px;border-radius:50%;background:#e2b533;border:4px solid #f4d35e}
.slider-arrows{position:absolute;left:358px;top:255px;display:flex;gap:5px}

.feature-tiles{position:absolute;left:102px;top:475px;display:flex}
.tile{width:270px;height:167px;color:var(--white);text-align:center;padding-top:22px}
.tile svg{display:block;margin:0 auto 12px}
.tile-title{font-size:20px;font-weight:300;margin-bottom:12px}
.tile-note{font-size:15px;font-weight:300;opacity:.92}
.tile-create{background:var(--tile-red)}
.tile-designs{background:var(--tile-gold)}
.tile-shirts{background:var(--tile-blue)}

.intro{position:absolute;left:102px;top:684px;width:812px;text-align:center}
.intro h1{font-size:21px;font-weight:400;color:var(--teal-text);margin-bottom:13px}
.intro p{font-size:11px;line-height:25.3px;color:#444}

.promo-band{position:absolute;left:0;top:831px;width:1016px;height:282px;background:var(--grey-band);border-top:2px solid #e3e3e3}
.promo{position:absolute;top:16px;width:240px}
.promo h2{font-size:15px;font-weight:400;color:var(--teal-text);margin-bottom:24px;white-space:nowrap}
.promo-img{width:237px;height:97px;border-radius:4px;border:1px solid #ddd}
.promo p{margin-top:28px;font-size:11.3px;line-height:25.3px;color:#555}
.promo-1{left:101px}.promo-2{left:390px}.promo-3{left:675px}
.img-pets{background:linear-gradient(90deg,#f4f4f4,#c9c4bf 30%,#f1eef0 60%,#e4c1d8)}
.img-team{background:linear-gradient(90deg,#1f7b3d,#f4f4f4 45%,#e9e9e9 65%,#1f6a3a)}
.img-sorry{background:linear-gradient(90deg,#f0f0f0,#d7dcc0 40%,#f2f2f2 60%,#dde0c8)}

.site-footer{position:absolute;left:0;top:1113px;width:1016px;height:87px;background:var(--footer);color:var(--white);text-align:center}
.footer-links{display:flex;justify-content:center;gap:16px;margin-top:22px;font-size:12px}
.copyright{margin-top:15px;font-size:12px}
</style>
</head>
<body>

<header class="masthead">
  <a class="brand" href="#"><span>Pennolark</span><span class="brand-dot"></span></a>
  <div class="contact-row">
    <span class="phone">555-014-2290</span>
    <span class="chat">
      <svg width="20" height="22" viewBox="0 0 20 22"><path d="M0 0h20v15H8l-6 6v-6H0z" fill="#1b5f7a"/></svg>
      Live Chat
    </span>
    <span class="social" style="background:#2aa8e0"></span>
    <span class="social" style="background:#27418c"></span>
    <span class="social" style="background:#c8201e"></span>
    <span class="social" style="background:#1c5c9c"></span>
  </div>
  <nav class="top-links"><a href="#">Design &amp; Buy</a><a href="#">Products</a><a href="#">Online Quote</a><a href="#">Design Templates</a></nav>
</header>

<nav class="mainnav">
  <div class="category-links"><a href="#">T-SHIRTS</a><a href="#">POLO SHIRTS</a><a href="#">SWEATSHIRTS</a><a href="#">HATS &amp; CAPS</a><a href="#">JERSEYS</a></div>
  <div class="account-links">
    <a href="#">Register</a><span class="sep">|</span><a href="#">Login</a><span class="sep">|</span><a href="#">Your Shooping cart</a>
    <svg width="16" height="14" viewBox="0 0 16 14"><path d="M1 1h3l2 8h8l1-6H5" fill="none" stroke="#fff" stroke-width="1.2"/><circle cx="7" cy="12" r="1.2" fill="#fff"/><circle cx="13" cy="12" r="1.2" fill="#fff"/></svg>
    <span>0 Items</span>
  </div>
</nav>

<section class="hero">
  <div class="hero-photo" role="img" aria-label="Photo of a smiling young man in a grey t-shirt with arms crossed"></div>
  <h2 class="hero-title">CUSTOM T-SHIRTS ONLINE</h2>
  <p class="hero-sub">With Your Text, Clip Art or Photos</p>
  <p class="hero-tag">It's Like Magic</p>
  <div class="trust-badge"></div>
  <div class="slider-arrows">
    <svg width="29" height="29" viewBox="0 0 29 29"><circle cx="14.5" cy="14.5" r="13" fill="#ddd" stroke="#fff" stroke-width="2"/><path d="M17 8l-6 6.5 6 6.5" fill="none" stroke="#fff" stroke-width="2"/></svg>
    <svg width="29" height="29" viewBox="0 0 29 29"><circle cx="14.5" cy="14.5" r="13" fill="#ddd" stroke="#fff" stroke-width="2"/><path d="M12 8l6 6.5-6 6.5" fill="none" stroke="#fff" stroke-width="2"/></svg>
  </div>
</section>

<section class="feature-tiles">
  <a class="tile tile-create" href="#">
    <svg width="46" height="46" viewBox="0 0 46 46"><path d="M4 42L30 16" stroke="#fff" stroke-width="5" stroke-linecap="round"/><path d="M36 4l2 5 5 2-5 2-2 5-2-5-5-2 5-2z" fill="#fff"/></svg>
    <div class="tile-title">YOU CREATE</div>
    <div class="tile-note">Click here to view</div>
  </a>
  <a class="tile tile-designs" href="#">
    <svg width="54" height="46" viewBox="0 0 54 46"><circle cx="27" cy="26" r="7" fill="#fff"/><g fill="#fff"><circle cx="27" cy="6" r="5"/><circle cx="14" cy="10" r="5"/><circle cx="40" cy="10" r="5"/><circle cx="7" cy="22" r="5"/><circle cx="47" cy="22" r="5"/><circle cx="12" cy="36" r="4"/><circle cx="42" cy="36" r="4"/><circle cx="27" cy="41" r="4"/></g></svg>
    <div class="tile-title">DESIGNS</div>
    <div class="tile-note">View all in house designs</div>
  </a>
  <a class="tile tile-shirts" href="#">
    <svg width="66" height="50" viewBox="0 0 66 50"><path d="M22 2h22l20 10-7 12-8-4v30H17V20l-8 4-7-12z" fill="#fff"/></svg>
    <div class="tile-title">T-SHIRTS</div>
    <div class="tile-note">View T-Shirt Colors &amp; Styles</div>
  </a>
</section>

<section class="intro">
  <h1>CUSTOM T-SHIRT PRINTING</h1>
  <p>Pennolark stated with an ambitious goal to create a different way to customize shirts. With the trend of everyone wanting custom apparel we wanted to create a platform to allow individuals to be their own fashion designer. We allow each visitor to add their own artwork, add text or use clip art from our gallery. So if you want to be the next t shirt fashion designer you can start here!</p>
</section>

<section class="promo-band">
  <article class="promo promo-1">
    <h2>DESIGN &amp; BUY</h2>
    <div class="promo-img img-pets" role="img" aria-label="White t-shirts printed with a dog in a hat and a cat in a pink boa"></div>
    <p>Here at Pennolark you can create your own shirt designs. You can easily upload personal artwork, pictures, logos, quotes or funny</p>
  </article>
  <article class="promo promo-2">
    <h2>SELL YOUR OWN DESIGNS</h2>
    <div class="promo-img img-team" role="img" aria-label="Green and white raglan shirt and green cap with a printed team name"></div>
    <p>Here at Pennolark you can create your own shirt designs. You can easily upload personal artwork, pictures, logos, quotes or funny</p>
  </article>
  <article class="promo promo-3">
    <h2>DESIGN CUSTOM SWEATSHIRTS</h2>
    <div class="promo-img img-sorry" role="img" aria-label="White shirts printed with green lettering"></div>
    <p>Here at Pennolark you can create your own shirt designs. You can easily upload personal artwork, pictures, logos, quotes or funny</p>
  </article>
</section>

<footer class="site-footer">
  <nav class="footer-links"><a href="#">My Account</a><a href="#">Terms of Service</a><a href="#">Returns Policy</a><a href="#">Privacy Policy</a><a href="#">Shipping</a><a href="#">Affiliate</a><a href="#">Create Event</a><a href="#">Religious Brands</a><a href="#">Contact</a><a href="#">Blog</a><a href="#">Sitemap</a></nav>
  <p class="copyright">Copyright © 2014 Pennolark.com</p>
</footer>

</body>
</html>
```